Real Estate - Property Management Prospectus/Brochure

We need a prospectus made up, around 9-10 pages including the cover page pages 3 onwards can be all a similar template happy for the front cover to have lots of black. I would like it to look very classy and futuristic, high end, blacks, silvers and whites, i am specializing in managing high end rental properties. i would like to design to correspond with the logo. I need to be able to email this booklet mostly - and also be able to print and mail out as well. I would like it crisp and clean as well - not to much on a page. Please note - happy for the cover to be simple with the logo added - prefer lots of black and with the other pages - they can all be a similar layout template to make this job easier? My website is www.leasemeridian.com.au and phone is 0418 293 547 email is tmarsh@leasemeridian.com.au
Target Market(s)
Investors
Industry/Entity Type
Real Estate
Requirements
Should not have
- Bright greens or bold colours

```html
<!DOCTYPE html>
<html lang="en">
<head>
<meta charset="utf-8">
<title>Lease Meridian – Property Management Prospectus</title>
<link href="https://fonts.googleapis.com/css2?family=Lato:wght@400;700&display=swap" rel="stylesheet">
<style>
  :root {
    --backdrop: #e4e4e4;
    --ink-black: #050505;
    --band-black: #0b0b0b;
    --silver: #c9c9c9;
    --silver-soft: #9a9a9a;
    --white: #ffffff;
    --text-light: #e6e6e6;
    --text-muted: #a8a8a8;
  }
  * { margin: 0; padding: 0; box-sizing: border-box; }
  html, body { width: 1072px; height: 1200px; overflow: hidden; }
  body {
    background: var(--backdrop);
    font-family: "Lato", "Helvetica Neue", Arial, sans-serif;
    position: relative;
  }
  .spread {
    position: absolute;
    left: 154px;
    width: 764px;
    height: 545px;
    overflow: hidden;
    background: var(--ink-black);
    box-shadow: 0 2px 8px rgba(0,0,0,0.25);
  }
  .spread--cover { top: 33px; }
  .spread--intro { top: 609px; }
  .spread svg { position: absolute; inset: 0; width: 100%; height: 100%; }
  .fold {
    position: absolute; left: 381px; top: 0; width: 2px; height: 100%;
    background: linear-gradient(90deg, rgba(255,255,255,0.04), rgba(0,0,0,0.25));
  }
  .brand-name {
    position: absolute;
    display: flex; align-items: center; gap: 7px;
    font-weight: 400; text-transform: uppercase; white-space: nowrap;
  }
  .brand-mark { display: inline-block; background: currentColor; }
  .brand-name--back { left: 22px; top: 470px; font-size: 12px; letter-spacing: 2px; color: var(--ink-black); }
  .brand-name--back .brand-mark { width: 8px; height: 8px; }
  .brand-name--front { left: 432px; top: 450px; font-size: 17px; letter-spacing: 3.5px; color: var(--silver); }
  .brand-name--front .brand-mark { width: 11px; height: 11px; }
  .contact {
    position: absolute; left: 219px; top: 465px;
    font-size: 9px; line-height: 12.5px; color: var(--text-light);
  }
  .cover-web {
    position: absolute; left: 432px; top: 502px;
    font-size: 12px; letter-spacing: 0.6px; color: var(--silver-soft);
  }
  .intro-column { position: absolute; top: 412px; color: var(--text-light); }
  .intro-column--left { left: 30px; width: 326px; }
  .intro-column--right { left: 417px; width: 332px; }
  .intro-heading { font-size: 14px; font-weight: 700; color: var(--white); margin-bottom: 10px; }
  .intro-body { font-size: 9.6px; line-height: 12.4px; text-align: justify; }
</style>
</head>
<body>

<section class="spread spread--cover" aria-label="Brochure cover spread">
  <svg viewBox="0 0 764 545" preserveAspectRatio="none">
    <defs>
      <linearGradient id="coastTone" x1="0" y1="0" x2="0" y2="1">
        <stop offset="0" stop-color="#f2f2f2"/>
        <stop offset="0.45" stop-color="#d9d9d9"/>
        <stop offset="0.6" stop-color="#9d9d9d"/>
        <stop offset="1" stop-color="#e8e8e8"/>
      </linearGradient>
      <linearGradient id="towerTone" x1="0" y1="0" x2="0" y2="1">
        <stop offset="0" stop-color="#c8c8c8"/>
        <stop offset="0.45" stop-color="#a8a8a8"/>
        <stop offset="0.7" stop-color="#5a5a5a"/>
        <stop offset="1" stop-color="#8c8c8c"/>
      </linearGradient>
      <linearGradient id="bandTone" x1="0" y1="0" x2="0" y2="1">
        <stop offset="0" stop-color="#030303"/>
        <stop offset="0.5" stop-color="#0e0e0e"/>
        <stop offset="1" stop-color="#080808"/>
      </linearGradient>
    </defs>
    <rect x="0" y="0" width="764" height="545" fill="url(#coastTone)" role="img" aria-label="Black and white aerial photo of a coastline with beach and high-rise buildings"/>
    <polygon points="460,0 764,0 764,545 657,545" fill="url(#towerTone)" role="img" aria-label="Black and white photo of a tall residential tower rising above a city skyline"/>
    <polygon points="8,0 472,0 669,545 207,545" fill="url(#bandTone)" role="img" aria-label="Darkened city skyline photo behind the black cover band"/>
    <line x1="0" y1="0" x2="199" y2="545" stroke="var(--silver)" stroke-width="3"/>
    <line x1="478" y1="0" x2="675" y2="545" stroke="var(--silver)" stroke-width="3"/>
  </svg>
  <div class="fold"></div>
  <div class="brand-name brand-name--back"><span class="brand-mark"></span>Lease Meridian</div>
  <div class="contact">
    P: 0418 293 547<br>
    E: tmarsh@leasemeridian.com.au<br>
    W: www.leasemeridian.com.au
  </div>
  <div class="brand-name brand-name--front"><span class="brand-mark"></span>Lease Meridian</div>
  <div class="cover-web">www.leasemeridian.com.au</div>
</section>

<section class="spread spread--intro" aria-label="Introduction spread">
  <svg viewBox="0 0 764 545" preserveAspectRatio="none">
    <defs>
      <linearGradient id="nightTone" x1="0" y1="0" x2="0" y2="1">
        <stop offset="0" stop-color="#2a2a2a"/>
        <stop offset="0.2" stop-color="#4a4a4a"/>
        <stop offset="0.33" stop-color="#6b6b6b"/>
        <stop offset="0.4" stop-color="#2c2c2c"/>
        <stop offset="0.5" stop-color="#5a5a5a"/>
        <stop offset="0.62" stop-color="#1a1a1a"/>
        <stop offset="0.75" stop-color="#050505"/>
        <stop offset="1" stop-color="#030303"/>
      </linearGradient>
    </defs>
    <rect x="0" y="0" width="764" height="545" fill="url(#nightTone)" role="img" aria-label="Black and white night photo of a city skyline reflected in still water"/>
  </svg>
  <div class="fold"></div>
  <div class="intro-column intro-column--left">
    <h2 class="intro-heading">Introduction</h2>
    <p class="intro-body">Lease Meridian was founded on the belief that investment property management should deliver results that go beyond our client's expectations. Lease Meridian is building a reputation by excelling in every aspect of the property management process, bringing innovation, confidence, and creativeness with an unparalleled commitment to excellence, these values echo in all aspects of Lease Meridian.</p>
  </div>
  <div class="intro-column intro-column--right">
    <h2 class="intro-heading">Meeting me – introduction to staff?? Principal/director</h2>
    <p class="intro-body">Tamsin is an industry expert with a history of excellence in property management, with over 12 years experience and a track record of success. Tamsin approaches her career with intensity, originality and enthusiasm. Her forward-thinking, innovative attitude offers clients a professional, efficient and a friendly management experience.</p>
  </div>
</section>

</body>
</html>
```